HARBORLINE AUTO GLASS

Mobile Glass Shop:

1) Windshield REPAIR 2)Windshield replacment 3) Rear Windshield Replacment 4) Side Window Replacment 5) car window replacment 6) Power Window Repair.

Schedual a service within 24 hour with one of our certified technicians.
Updates

See "brightvane auto repair" web site for referance on the nature of our buisness and service. www.brightvane-example.com

Coding

```html
<!DOCTYPE html>
<html lang="en">
<head>
<meta charset="utf-8">
<title>Contact Us – Harborline Auto Glass</title>
<link href="https://fonts.googleapis.com/css2?family=Bebas+Neue&family=Poppins:wght@400;500;600&display=swap" rel="stylesheet">
<style>
:root{
  --blue:#2a86c4;
  --blue-light:#5a9cca;
  --blue-deep:#1c5f94;
  --ink:#222;
  --muted:#444;
  --dark:#232427;
  --red:#e0262a;
  --white:#fff;
  --line:#d9d9d9;
}
*{margin:0;padding:0;box-sizing:border-box}
html,body{width:680px;height:1200px;overflow:hidden;background:var(--white)}
body{position:relative;font-family:"Poppins",sans-serif;color:var(--ink)}
.abs{position:absolute}
.display{font-family:"Bebas Neue",sans-serif;letter-spacing:.5px}

/* header */
.brand{left:38px;top:22px;display:flex;align-items:center;gap:6px}
.brand-mark{width:26px;height:26px;background:var(--blue)}
.brand-name{font-family:"Poppins",sans-serif;font-weight:600;font-size:11px;color:var(--blue);line-height:1.1;letter-spacing:.5px}
.nav{top:35px;left:224px;display:flex;gap:0;font-size:8px;color:#333}
.nav span{position:absolute;white-space:nowrap}
.nav .active{color:var(--blue);font-weight:600}
.nav .active::after{content:"";position:absolute;left:6px;right:6px;top:12px;border-bottom:1.5px dotted var(--blue)}
.callnow{left:520px;top:20px;display:flex;gap:6px;align-items:center}
.callnow .lbl{font-family:"Bebas Neue",sans-serif;font-size:10px;color:#222;line-height:1}
.callnow .num{font-family:"Bebas Neue",sans-serif;font-size:16px;color:var(--blue);line-height:1}

/* hero */
.hero{left:0;top:74px;width:680px;height:232px;background:linear-gradient(90deg,#4d92c6,#5c9fcd 45%,#3f7fb3)}
.hero-photo{left:315px;top:0;width:365px;height:232px;background:linear-gradient(120deg,#7fb5dc,#3a6fa2 55%,#27456e)}
.hero-title{left:63px;top:100px;font-size:22px;color:var(--white);letter-spacing:1.5px}

/* contact */
.section-title{top:357px;left:0;width:680px;text-align:center;font-size:17px;color:#111}
.section-rule{top:389px;left:333px;width:33px;height:1px;background:#333}
.info{left:91px;display:flex;gap:8px}
.info .ico{width:22px;height:22px;border-radius:50%;background:var(--blue);display:flex;align-items:center;justify-content:center;flex:none}
.info h3{font-family:"Bebas Neue",sans-serif;font-weight:400;font-size:11px;color:#111;line-height:1}
.info p{font-size:7.5px;color:#222;line-height:1.25}
.map{left:350px;top:432px;width:234px;height:198px;background:linear-gradient(135deg,#f1f1f1,#e6e6e6)}

/* banner */
.banner{left:85px;top:711px;width:553px;height:145px;border-radius:6px;background:linear-gradient(90deg,#1b6eab,#2b8ccb 55%,#58a7d8)}
.van{left:51px;top:682px;width:246px;height:200px;border-radius:18px;background:linear-gradient(160deg,#fafafa,#dfe4e8 70%,#bfc6cc)}
.tech{left:451px;top:656px;width:193px;height:200px;border-radius:80px 80px 6px 6px;background:linear-gradient(180deg,#2b4f7c,#1d3658)}
.promo{left:290px;top:731px;width:162px;text-align:center;color:var(--white)}
.promo .t1{font-family:"Bebas Neue",sans-serif;font-size:17px;letter-spacing:1.5px;line-height:1}
.promo .t2{font-family:"Poppins",sans-serif;font-style:italic;font-weight:600;font-size:29px;line-height:1.1;margin-top:2px;display:flex;justify-content:center;align-items:center;gap:4px}
.promo .t3{font-size:8px;line-height:1.3;margin-top:2px}
.promo .t3 b{font-weight:600}
.pill{left:316px;top:812px;width:120px;height:30px}
.pill .circle{position:absolute;left:0;top:0;width:30px;height:30px;border-radius:50%;background:var(--red);display:flex;align-items:center;justify-content:center}
.pill .tag{position:absolute;left:28px;top:1px;background:var(--red);color:var(--white);font-family:"Bebas Neue",sans-serif;font-size:7px;padding:1px 6px 0 8px;border-radius:0 6px 0 0}
.pill .num{position:absolute;left:26px;top:12px;width:92px;height:15px;background:#0f3f69;color:var(--white);font-family:"Bebas Neue",sans-serif;font-size:13px;line-height:15px;padding-left:9px;border-radius:0 0 6px 0}

/* footer */
.f-brand{left:36px;top:990px;display:flex;align-items:center;gap:8px}
.f-brand .brand-mark{width:34px;height:34px}
.f-brand .brand-name{font-size:14px;color:#3e9ad8}
.f-ico{width:24px;height:24px;border-radius:50%;background:var(--blue);display:flex;align-items:center;justify-content:center}
.f-phone{left:70px;top:1049px;font-family:"Bebas Neue",sans-serif;color:var(--red);font-size:20px;line-height:1}
.f-mail{left:71px;top:1071px;font-size:7.5px;color:var(--blue)}
.f-addr{left:72px;top:1089px;font-size:7.5px;color:var(--white);line-height:1.2}
.f-head{font-family:"Poppins",sans-serif;font-weight:500;font-size:10.5px;letter-spacing:1.5px;color:var(--white)}
.f-dash{font-size:9px;color:#bbb;letter-spacing:2px}
.f-list{list-style:none;font-size:7.5px;color:var(--white);line-height:15.3px}
.f-list li::before{content:"-";margin-right:7px}
.field{position:absolute;border:1px solid #555;font-size:7px;font-style:italic;color:#aaa;padding:2px 4px;border-radius:2px}
.submit{left:466px;top:1090px;width:82px;height:21px;border-radius:11px;background:var(--blue);color:var(--white);font-size:7.5px;text-align:center;line-height:21px}

.copy{left:42px;top:1170px;font-size:7.5px;color:#333}
.social{top:1164px;width:22px;height:22px;border-radius:50%;background:#222}
.social.first{background:var(--blue)}
</style>
</head>
<body>

<!-- header -->
<div class="abs brand">
  <div class="brand-mark"></div>
  <div class="brand-name">HARBORLINE<br>AUTO GLASS</div>
</div>
<nav class="abs nav" aria-label="Main">
  <span style="left:0">Home</span>
  <span style="left:41px">About</span>
  <span style="left:84px">Services</span>
  <span style="left:135px">Insurance</span>
  <span style="left:193px">Gallery</span>
  <span class="active" style="left:240px">Contact</span>
</nav>
<div class="abs callnow">
  <svg width="26" height="26" viewBox="0 0 24 24" fill="none" stroke="#2a86c4" stroke-width="1.6"><path d="M5 3h3l2 5-2 1.5a11 11 0 0 0 6.5 6.5L16 14l5 2v3a2 2 0 0 1-2 2A17 17 0 0 1 3 5a2 2 0 0 1 2-2z"/></svg>
  <div><div class="lbl">CALL US NOW</div><div class="num">000 123 456 789</div></div>
</div>

<!-- hero -->
<section class="abs hero">
  <div class="abs hero-photo" role="img" aria-label="Technician lifting a windshield with suction cups"></div>
  <h1 class="abs hero-title display">CONTACT US</h1>
  <svg class="abs" style="left:0;top:0" width="680" height="232" viewBox="0 0 680 232">
    <path d="M0 188 Q340 285 680 188 L680 232 L0 232 Z" fill="#2a86c4"/>
    <path d="M0 225 Q90 200 340 214 Q590 200 680 225 L680 232 L0 232 Z" fill="#fff"/>
    <path d="M318 232 Q340 210 362 232 Z" fill="#fff"/>
    <path d="M336 228 l4 3.5 4-3.5 M336 224 l4 3.5 4-3.5" stroke="#222" stroke-width="1.3" fill="none"/>
  </svg>
</section>

<!-- contact -->
<h2 class="abs section-title display">GET IN TOUCH WITH US</h2>
<div class="abs section-rule"></div>

<div class="abs info" style="top:447px">
  <div class="ico"><svg width="11" height="11" viewBox="0 0 24 24" fill="#fff"><path d="M5 3h3l2 5-2 1.5a11 11 0 0 0 6.5 6.5L16 14l5 2v3a2 2 0 0 1-2 2A17 17 0 0 1 3 5a2 2 0 0 1 2-2z"/></svg></div>
  <div><h3>CALL US</h3><p>Telephone &nbsp;: 000 123 456 789</p></div>
</div>
<div class="abs info" style="top:512px">
  <div class="ico"><svg width="11" height="11" viewBox="0 0 24 24" fill="none" stroke="#fff" stroke-width="2"><rect x="3" y="6" width="18" height="12"/><path d="M3 6l9 7 9-7"/></svg></div>
  <div><h3>MAIL US</h3><p>E-Mail &nbsp;: info@harborlineautoglass.com</p></div>
</div>
<div class="abs info" style="top:576px">
  <div class="ico"><svg width="10" height="10" viewBox="0 0 24 24" fill="#fff"><path d="M12 2a7 7 0 0 0-7 7c0 5 7 13 7 13s7-8 7-13a7 7 0 0 0-7-7zm0 9.5a2.5 2.5 0 1 1 0-5 2.5 2.5 0 0 1 0 5z"/></svg></div>
  <div><h3>ADDRESS</h3><p>48 Tideway Ave<br>#210, Atlanta, GA 12345</p></div>
</div>
<div class="abs map" role="img" aria-label="Street map showing the shop location"></div>

<!-- schedule banner -->
<div class="abs banner"></div>
<div class="abs van" role="img" aria-label="White service van in company colours"></div>
<div class="abs tech" role="img" aria-label="Smiling technician holding keys and a clipboard"></div>
<div class="abs promo">
  <div class="t1">SCHEDUAL A SERVICE</div>
  <div class="t2">24hr
    <svg width="28" height="28" viewBox="0 0 24 24" fill="none" stroke="#fff" stroke-width="2"><circle cx="12" cy="12" r="9"/><path d="M12 7v5l-3 2"/></svg>
  </div>
  <div class="t3">WITH ONE OF OUR <b>CERTIFIED<br>TECHNICIANS</b></div>
</div>
<div class="abs pill">
  <div class="tag">CALL NOW</div>
  <div class="num">000 123 456 789</div>
  <div class="circle"><svg width="14" height="14" viewBox="0 0 24 24" fill="#fff"><path d="M5 3h3l2 5-2 1.5a11 11 0 0 0 6.5 6.5L16 14l5 2v3a2 2 0 0 1-2 2A17 17 0 0 1 3 5a2 2 0 0 1 2-2z"/></svg></div>
</div>

<!-- footer -->
<svg class="abs" style="left:0;top:900px" width="680" height="254" viewBox="0 0 680 254">
  <path d="M0 3 Q340 80 680 3 L680 254 L0 254 Z" fill="#232427"/>
</svg>

<div class="abs f-brand">
  <div class="brand-mark"></div>
  <div class="brand-name">HARBORLINE<br>AUTO GLASS</div>
</div>
<div class="abs f-ico" style="left:41px;top:1051px"><svg width="11" height="11" viewBox="0 0 24 24" fill="#fff"><path d="M5 3h3l2 5-2 1.5a11 11 0 0 0 6.5 6.5L16 14l5 2v3a2 2 0 0 1-2 2A17 17 0 0 1 3 5a2 2 0 0 1 2-2z"/></svg></div>
<div class="abs f-phone">000 123 456 789</div>
<div class="abs f-mail">info@harborlineautoglass.com</div>
<div class="abs f-ico" style="left:41px;top:1083px"><svg width="10" height="10" viewBox="0 0 24 24" fill="#fff"><path d="M12 2a7 7 0 0 0-7 7c0 5 7 13 7 13s7-8 7-13a7 7 0 0 0-7-7zm0 9.5a2.5 2.5 0 1 1 0-5 2.5 2.5 0 0 1 0 5z"/></svg></div>
<div class="abs f-addr">48 Tideway Ave<br>#210, Atlanta, GA 12345</div>

<div class="abs f-dash" style="left:215px;top:1006px">-----</div>
<ul class="abs f-list" style="left:214px;top:1022px">
  <li>Home</li><li>About</li><li>Services</li><li>Insurance</li><li>Gallery</li><li>Contact</li>
</ul>

<div class="abs f-head" style="left:307px;top:991px">SERVICES</div>
<div class="abs f-dash" style="left:307px;top:1006px">-----</div>
<ul class="abs f-list" style="left:308px;top:1022px">
  <li>Windshield Repair</li><li>Windshield Replacment</li><li>Rear Windshield Replacment</li><li>Side Window Replacment</li><li>Car Window Teplacment</li><li>Power Window Repair</li>
</ul>

<div class="abs f-head" style="left:464px;top:991px">QUICK CONTACT</div>
<div class="abs f-dash" style="left:465px;top:1006px">-----</div>
<div class="field" style="left:465px;top:1026px;width:54px;height:15px">Name*</div>
<div class="field" style="left:523px;top:1026px;width:54px;height:15px">Phone*</div>
<div class="field" style="left:582px;top:1026px;width:54px;height:15px">Email*</div>
<div class="field" style="left:465px;top:1045px;width:171px;height:38px">Message</div>
<div class="abs submit">SUBMIT</div>

<!-- bottom bar -->
<div class="abs copy">Copyright © HARBORLINE AUTO GLASS. All Rights Reserved.</div>
<div class="abs social first" style="left:533px" aria-label="Social profile"></div>
<div class="abs social" style="left:560px" aria-label="Social profile"></div>
<div class="abs social" style="left:587px" aria-label="Social profile"></div>
<div class="abs social" style="left:615px" aria-label="Social profile"></div>

</body>
</html>
```